TLK Electricial Contracting Services

Hi guys, after a design for my small electrical company, have logo design files to be incorporated into the layout, the basic concept is electrical contracting services for residential, commercial, industrial & data services, image is clean clear and strong,

Card format is to have a nice clean logo on front,with maybe the Residential – commercial – industrial - data, followed with licensed & insured, followed by contact details on backside of the card.

Target Market(s)

Residential, commercial, industrial sectors.

Industry/Entity Type

Electrical

Contact Information for Business Card

TLK logo,
Residential – commercial – industrial - data
REC: 61307
Email: tlk@vornamail.net.au
Phone: 0487 352 019

Requirements
Must have
• Clean & strong design.
Nice to have
• If possible, I would like the logo colours inverted so the text is orange and the background is black on the front of the card, then the backside of the card be the reverse colour
Should not have
• No Sparks, lightning bolts,

```html
<!DOCTYPE html>
<html lang="en">
<head>
<meta charset="utf-8">
<title>TLK Electrical – Business Card</title>
<link rel="stylesheet" href="https://fonts.googleapis.com/css2?family=Raleway:wght@300;400;700&display=swap">
<style>
  :root {
    --backdrop: #1b1b1c;
    --card: #2e2f33;
    --orange: #f2892c;
    --text-light: #d2d2d4;
    --text-white: #ececee;
  }
  * { margin: 0; padding: 0; box-sizing: border-box; }
  html, body {
    width: 1200px;
    height: 900px;
    overflow: hidden;
    background: var(--backdrop);
    font-family: "Raleway", Arial, sans-serif;
  }
  .stage { position: relative; width: 1200px; height: 900px; }

  .card {
    position: absolute;
    background: var(--card);
    border-radius: 14px;
  }
  .card--details { left: 330px; top: 116px; width: 555px; height: 320px; }
  .card--brand   { left: 332px; top: 489px; width: 541px; height: 314px; }

  .brand {
    position: absolute;
    color: var(--orange);
    font-weight: 700;
    line-height: 1;
    display: flex;
    flex-direction: column;
  }
  .brand__mark { letter-spacing: 1px; }
  .brand__name { letter-spacing: 0.4px; }

  .card--details .brand { left: 54px; top: 118px; }
  .card--details .brand__mark { font-size: 86px; }
  .card--details .brand__name { font-size: 15px; margin-top: 8px; }

  .card--brand .brand { left: 0; right: 0; top: 78px; align-items: center; }
  .card--brand .brand__mark { font-size: 104px; }
  .card--brand .brand__name { font-size: 18px; margin-top: 8px; }

  .services {
    position: absolute;
    left: 0;
    right: 0;
    top: 228px;
    text-align: center;
    color: var(--text-light);
    font-size: 13px;
    font-weight: 400;
    letter-spacing: 1.2px;
    line-height: 20px;
  }
  .services__note {
    color: var(--orange);
    font-weight: 700;
    font-size: 12px;
    letter-spacing: 2px;
    text-transform: uppercase;
  }

  .contact {
    position: absolute;
    left: 292px;
    top: 112px;
  }
  .contact__name {
    color: var(--orange);
    font-size: 26px;
    font-weight: 400;
    line-height: 1.1;
  }
  .contact__role {
    color: var(--text-light);
    font-size: 16px;
    font-weight: 300;
    margin-top: 2px;
  }
  .contact__lines {
    list-style: none;
    margin-top: 20px;
    margin-left: 4px;
    color: var(--text-white);
    font-size: 15px;
    font-weight: 400;
    line-height: 20px;
  }
</style>
</head>
<body>
  <main class="stage">
    <section class="card card--details">
      <div class="brand">
        <span class="brand__mark">TLK</span>
        <span class="brand__name">Tolan Kerr Electrical</span>
      </div>
      <div class="contact">
        <p class="contact__name">Daniel Reeve</p>
        <p class="contact__role">Managing Director</p>
        <ul class="contact__lines">
          <li>tlk@vornamail.net.au</li>
          <li>0487 352 019</li>
          <li>REC: 61307</li>
        </ul>
      </div>
    </section>

    <section class="card card--brand">
      <div class="brand">
        <span class="brand__mark">TLK</span>
        <span class="brand__name">Tolan Kerr Electrical</span>
      </div>
      <div class="services">
        <p class="services__list">Residential – Commercial – Industrial – Data</p>
        <p class="services__note">Licensed &amp; Insured</p>
      </div>
    </section>
  </main>
</body>
</html>
```